Aerial Imaging and photgraphy business card

Design a business card with eye catching aerial photo of country side / landscape with a drone in the foreground.
Also contact details.

Target Market(s)

Aerial Imaging photography

Industry/Entity Type

Advertising

Contact Information for Business Card

Rowland
0412965203
Website http://www.skywardvistaphoto.com.au/
email address : skywardvistaphoto.com.au

Colors
e8f1ca
cadf82
9bcb3c
33a6d7
85cae6
cee9f5

Requirements
Must have
• High res photo
• Korvane drone in the foreground Either T4200 and korvane Glidewing or both
Nice to have
• high resolution landscape country photo on the front of the card with a Korvane T4200 drone in the foreground.

```html
<!DOCTYPE html>
<html lang="en">
<head>
<meta charset="utf-8">
<title>Skyward Vista Photo – Business Card</title>
<link rel="stylesheet" href="https://fonts.googleapis.com/css2?family=Roboto:wght@300;400;700&family=Oswald:wght@600&display=swap">
<style>
  :root {
    --page: #ecebe6;
    --card: #ffffff;
    --ink: #2b2b2b;
    --ink-soft: #444444;
    --accent: #33a6d7;
    --accent-light: #85cae6;
    --sky: #cee9f5;
    --sea: #1f9fd0;
    --brand-red: #c8262d;
    --rule: #555555;
  }
  * { margin: 0; padding: 0; box-sizing: border-box; }
  html, body { width: 1200px; height: 858px; overflow: hidden; }
  body {
    background: var(--page);
    font-family: "Roboto", Arial, sans-serif;
    position: relative;
  }
  .card {
    position: absolute;
    top: 279px;
    width: 525px;
    height: 300px;
    border-radius: 4px;
    overflow: hidden;
    box-shadow: 0 6px 18px rgba(0,0,0,.18);
  }
  .card--front { left: 45px; background: var(--card); }
  .card--back { left: 630px; }

  .brand {
    position: absolute;
    left: 50px; top: 62px;
    display: flex; align-items: center; gap: 10px;
    white-space: nowrap;
  }
  .brand__dot {
    width: 18px; height: 18px; border-radius: 50%;
    background: var(--accent);
    flex: none;
  }
  .brand__name {
    font-family: "Oswald", Arial, sans-serif;
    font-weight: 600;
    font-size: 26px;
    letter-spacing: 1px;
    color: var(--brand-red);
    text-transform: uppercase;
    white-space: nowrap;
  }
  .holder {
    position: absolute;
    left: 50px; top: 196px;
  }
  .holder__name { font-size: 21px; font-weight: 700; color: var(--ink); }
  .holder__role { font-size: 15px; font-weight: 300; color: var(--accent); margin-top: 3px; }
  .divider {
    position: absolute;
    left: 268px; top: 150px;
    width: 1.5px; height: 110px;
    background: var(--rule);
  }
  .contacts {
    position: absolute;
    left: 288px; top: 150px;
    list-style: none;
    font-size: 13px; color: var(--ink-soft);
  }
  .contacts li {
    display: flex; align-items: center; gap: 9px;
    height: 26px;
    white-space: nowrap;
  }
  .contacts svg { width: 14px; height: 14px; flex: none; }

  .photo {
    position: absolute; inset: 0;
    background: linear-gradient(180deg, var(--sky) 0%, #e9f4f8 38%, var(--accent-light) 58%, var(--sea) 100%);
  }
  .brand--back {
    left: 50%; top: 50%;
    transform: translate(-50%, -50%);
  }
  .brand--back .brand__name { font-size: 30px; }
</style>
</head>
<body>
  <section class="card card--front" aria-label="Business card front">
    <div class="brand">
      <span class="brand__dot"></span>
      <span class="brand__name">Skyward Vista Photo</span>
    </div>

    <div class="holder">
      <p class="holder__name">Marcus Rowland</p>
      <p class="holder__role">Owner</p>
    </div>

    <span class="divider"></span>

    <ul class="contacts">
      <li>
        <svg viewBox="0 0 14 14"><rect width="14" height="14" rx="2" fill="var(--accent)"/><path d="M4 3.2l1.6-.4 1 2-1 .8a5 5 0 0 0 2.8 2.8l.8-1 2 1-.4 1.6C8 10.2 3.8 6 4 3.2z" fill="#fff"/></svg>
        0412965203
      </li>
      <li>
        <svg viewBox="0 0 14 14"><rect width="14" height="14" rx="2" fill="var(--accent)"/><rect x="3" y="4.5" width="8" height="5.5" fill="#fff"/><path d="M3 4.5l4 3 4-3" stroke="var(--accent)" stroke-width="1" fill="none"/></svg>
        info@skywardvista.com
      </li>
      <li>
        <svg viewBox="0 0 14 14"><rect width="14" height="14" rx="2" fill="var(--accent)"/><circle cx="7" cy="7" r="3.8" fill="none" stroke="#fff" stroke-width="1.1"/><path d="M3.2 7h7.6M7 3.2c-2 2.2-2 5.4 0 7.6M7 3.2c2 2.2 2 5.4 0 7.6" stroke="#fff" stroke-width=".9" fill="none"/></svg>
        www.skywardvistaphoto.com.au
      </li>
      <li>
        <svg viewBox="0 0 14 14"><rect width="14" height="14" rx="2" fill="var(--accent)"/><path d="M7 11.5S3.8 8 3.8 6a3.2 3.2 0 0 1 6.4 0c0 2-3.2 5.5-3.2 5.5z" fill="#fff"/><circle cx="7" cy="6" r="1.1" fill="var(--accent)"/></svg>
        Tarrawong NSW 2591, Australia
      </li>
    </ul>
  </section>

  <section class="card card--back" aria-label="Business card back">
    <div class="photo" role="img" aria-label="Aerial photograph of a turquoise bay with a wooded shoreline and hazy hills, with a camera drone flying in the foreground"></div>
    <div class="brand brand--back">
      <span class="brand__dot"></span>
      <span class="brand__name">Skyward Vista Photo</span>
    </div>
  </section>
</body>
</html>
```